Lullaby Glimpse Studio advertisement rack card

Name of company:Lullaby Glimpse Studio Service provided : We do gender determination and 3D/4D ultrasounds Location: 7213 Orchard Road Pace Fl Phone :8503662088we also have the heartbeat bears for sale . I would like for all this info on the rack card and we are trying to reach pregnant women to use us to see there babies before they are born.

Target Market(s)

18 to 45 women

Industry/Entity Type

It Company

Font styles to use
Decorative

Requirements
Must have
• Bright colors and use the logo sent use at least on of the babies image in design Name of company:Lullaby Glimpse Studio Service provided : We do gender determination and 3D/4D ultrasounds Location: 7213 Orchard Road Pace Fl Phone :8503662088we also have the heartbeat bears for sale
Nice to have
• Use the pic of the Cuddle Pulse Bear in the corner of rack card to show we are a heartbeat dealer

```html
<!DOCTYPE html>
<html lang="en">
<head>
<meta charset="utf-8">
<title>Lullaby Glimpse Studio – Rack Card</title>
<link rel="stylesheet" href="https://fonts.googleapis.com/css2?family=Berkshire+Swash&family=Libre+Baskerville:wght@700&display=swap">
<style>
  :root {
    --rose: #cf4660;
    --rose-deep: #a9334a;
    --mist: #e3e3e3;
    --mist-light: #eeeeee;
    --leaf: #93b74e;
    --lagoon: #34a3a9;
    --marigold: #dba512;
    --white: #ffffff;
  }
  html, body {
    margin: 0;
    padding: 0;
    overflow: hidden;
    background: var(--white);
  }
  .rack-card {
    position: relative;
    width: 1200px;
    height: 2613px;
    overflow: hidden;
  }
  .rack-card__art {
    position: absolute;
    inset: 0;
  }
  .brand-script {
    font-family: "Berkshire Swash", cursive;
    fill: var(--white);
  }
  .brand-script--shadow {
    fill: var(--rose-deep);
  }
  .service-line {
    font-family: "Libre Baskerville", Georgia, serif;
    font-weight: 700;
    font-size: 30px;
    fill: var(--white);
    letter-spacing: 0.5px;
  }
  .dealer-line {
    font-family: "Libre Baskerville", Georgia, serif;
    font-weight: 700;
    font-size: 25px;
    fill: var(--rose);
  }
  .partner-name {
    font-family: "Berkshire Swash", cursive;
    font-size: 52px;
    fill: var(--white);
  }
</style>
</head>
<body>
<main class="rack-card">
  <svg class="rack-card__art" width="1200" height="2613" viewBox="0 0 1200 2613" xmlns="http://www.w3.org/2000/svg">
    <defs>
      <radialGradient id="portrait-shade" cx="0.5" cy="0.5" r="0.5">
        <stop offset="0" stop-color="#a9334a" stop-opacity="0.35"/>
        <stop offset="0.6" stop-color="#b43a51" stop-opacity="0.18"/>
        <stop offset="1" stop-color="#cf4660" stop-opacity="0"/>
      </radialGradient>
      <radialGradient id="lace-rose" cx="0.5" cy="0.5" r="0.5">
        <stop offset="0" stop-color="#e0667d" stop-opacity="0.55"/>
        <stop offset="1" stop-color="#cf4660" stop-opacity="0"/>
      </radialGradient>
      <radialGradient id="lace-white" cx="0.5" cy="0.5" r="0.5">
        <stop offset="0" stop-color="#f6f6f6" stop-opacity="0.95"/>
        <stop offset="1" stop-color="#e3e3e3" stop-opacity="0"/>
      </radialGradient>
    </defs>

    <!-- rose backdrop -->
    <rect class="backdrop" x="0" y="0" width="1200" height="2100" fill="var(--rose)"/>

    <!-- ultrasound portrait area -->
    <ellipse class="baby-portrait" cx="470" cy="1050" rx="560" ry="700" fill="url(#portrait-shade)"
             role="img" aria-label="Faint 3D ultrasound portrait of a baby"/>

    <!-- lace decoration on rose -->
    <ellipse class="lace lace--rose" cx="980" cy="1120" rx="360" ry="520" fill="url(#lace-rose)"
             role="img" aria-label="Soft lace flower pattern"/>
    <ellipse class="lace lace--rose-top" cx="1060" cy="260" rx="260" ry="320" fill="url(#lace-rose)"
             role="img" aria-label="Soft lace flower pattern"/>

    <!-- brand title -->
    <text class="brand-script brand-script--shadow" x="426" y="278" font-size="84" text-anchor="middle">Lullaby</text>
    <text class="brand-script" x="420" y="272" font-size="84" text-anchor="middle">Lullaby</text>
    <text class="brand-script brand-script--shadow" x="600" y="518" font-size="138" text-anchor="middle">Glimpse Studio</text>
    <text class="brand-script" x="592" y="510" font-size="138" text-anchor="middle">Glimpse Studio</text>

    <!-- tagline -->
    <text class="brand-script" x="272" y="622" font-size="64">Meet your baby</text>
    <text class="brand-script" x="437" y="712" font-size="56">before he/she is born!</text>

    <!-- service band -->
    <rect class="service-band" x="0" y="796" width="1200" height="108" fill="#ffffff" fill-opacity="0.14"/>
    <text class="service-line" x="600" y="862" text-anchor="middle">GENDER DETERMINATION AND 3D/4D ULTRASOUNDS</text>

    <!-- pale lower field -->
    <polygon class="lower-field" points="0,1460 296,1168 460,1322 607,1177 1200,1771 1200,2613 0,2613"
             fill="var(--mist)" stroke="var(--mist-light)" stroke-width="10"/>

    <!-- lace decoration on pale field -->
    <ellipse class="lace lace--white" cx="930" cy="2000" rx="420" ry="560" fill="url(#lace-white)"
             role="img" aria-label="White lace flower pattern"/>

    <!-- colour tiles -->
    <polygon class="tile tile--leaf" points="296,1190 576,1470 296,1750 16,1470"
             fill="var(--leaf)" stroke="var(--mist-light)" stroke-width="12"/>
    <polygon class="tile tile--lagoon" points="607,1190 900,1470 607,1756 330,1470"
             fill="var(--lagoon)" stroke="var(--mist-light)" stroke-width="12"/>
    <polygon class="tile tile--marigold" points="47,1526 330,1809 47,2092 -236,1809"
             fill="var(--marigold)" stroke="var(--mist-light)" stroke-width="12"/>

    <!-- partner mark -->
    <circle class="partner-seal" cx="910" cy="2287" r="188" fill="var(--rose)"/>
    <text class="partner-name" x="910" y="2272" text-anchor="middle">Cuddle</text>
    <text class="partner-name" x="910" y="2338" text-anchor="middle">Pulse Bear</text>

    <!-- dealer note -->
    <text class="dealer-line" x="100" y="2490">Authorized Cuddle Pulse Bear dealer</text>
  </svg>
</main>
</body>
</html>
```